New bussiness card, using company logo.
Lionel Brisk
Manager/Director
Brisk Property Developments
Po Box 5347
Ferndale Central
Vic
0491 638 205
lionel@briskpropertydevelopments
eye catching, vibrant colours, professional

```html
<!DOCTYPE html>
<html lang="en">
<head>
<meta charset="utf-8">
<title>Brisk Property Developments – Business Cards</title>
<link rel="stylesheet" href="https://fonts.googleapis.com/css2?family=Didact+Gothic&family=Michroma&display=swap">
<style>
  :root {
    --stage-dark: #1f1b24;
    --stage-mid: #3b3442;
    --card-white: #ffffff;
    --brand-red: #dd2a2f;
    --brand-green: #6ab845;
    --brand-green-light: #8fc63f;
    --ink: #2b2b2b;
    --ink-soft: #5a5a5a;
    --rule: #b9b9b9;
  }
  * { box-sizing: border-box; margin: 0; padding: 0; }
  html, body { width: 1200px; height: 767px; overflow: hidden; }
  body {
    position: relative;
    background: radial-gradient(ellipse at 50% 45%, var(--stage-mid) 0%, var(--stage-dark) 100%);
    font-family: "Didact Gothic", "Century Gothic", sans-serif;
  }
  .card {
    position: absolute;
    width: 531px;
    height: 303px;
    border-radius: 22px;
    overflow: hidden;
    box-shadow: 0 6px 18px rgba(0,0,0,.45);
  }
  .card--front   { left: 43px;  top: 45px;  background: var(--card-white); }
  .card--back    { left: 616px; top: 49px;  background: var(--card-white); }
  .card--green   { left: 46px;  top: 402px; background: linear-gradient(160deg, var(--brand-green) 0%, var(--brand-green-light) 100%); }
  .card--red     { left: 633px; top: 409px; background: var(--brand-red); }

  .wordmark {
    position: absolute;
    display: flex;
    align-items: center;
    gap: 12px;
    font-family: "Michroma", "Arial", sans-serif;
    font-weight: 400;
    line-height: 1.15;
    text-transform: uppercase;
  }
  .wordmark__square { width: 22px; height: 22px; flex: none; }
  .wordmark__name { display: block; }

  .card--front .wordmark { left: 38px; top: 62px; color: var(--brand-red); font-size: 21px; }
  .card--front .wordmark__square { background: var(--brand-green); }

  .card--back .wordmark,
  .card--green .wordmark,
  .card--red .wordmark {
    left: 0; right: 0; justify-content: center; font-size: 27px; text-align: left;
  }
  .card--back .wordmark  { top: 112px; color: var(--brand-red); }
  .card--back .wordmark__square { background: var(--brand-green); width: 28px; height: 28px; }
  .card--green .wordmark,
  .card--red .wordmark   { top: 126px; color: var(--card-white); }
  .card--green .wordmark__square,
  .card--red .wordmark__square { background: var(--card-white); width: 28px; height: 28px; }

  .card__divider {
    position: absolute; left: 0; right: 0; top: 193px; height: 3px;
    background: linear-gradient(90deg, rgba(185,185,185,0) 0%, var(--rule) 70%, var(--ink-soft) 100%);
  }
  .holder { position: absolute; right: 30px; text-align: right; }
  .holder__name  { top: 166px; color: var(--brand-red); font-size: 21px; }
  .holder__role  { top: 198px; color: var(--brand-green); font-size: 16px; letter-spacing: .3px; }

  .contact {
    position: absolute; left: 42px; top: 208px;
    list-style: none; color: var(--ink); font-size: 15px;
  }
  .contact li { display: flex; align-items: center; gap: 6px; height: 29px; }
  .contact svg { flex: none; }
  .contact li:nth-child(2) { font-size: 14px; }

  .website {
    position: absolute; left: 0; right: 0; text-align: center;
    font-size: 14px; letter-spacing: 2.6px;
  }
  .card--back .website  { top: 265px; color: var(--ink-soft); }
  .website__accent { color: var(--brand-red); }
  .card--green .website { top: 248px; color: var(--card-white); }
  .card--red .website   { top: 248px; color: var(--card-white); }
</style>
</head>
<body>

<section class="card card--front" aria-label="Business card front">
  <div class="wordmark">
    <span class="wordmark__square"></span>
    <span class="wordmark__name">Brisk Property<br>Developments</span>
  </div>
  <p class="holder holder__name">Lionel Brisk</p>
  <div class="card__divider"></div>
  <p class="holder holder__role">Manager/Director</p>
  <ul class="contact">
    <li>
      <svg width="11" height="12" viewBox="0 0 11 12" aria-hidden="true"><path d="M2 0.5 L4 0.5 L4.8 3.4 L3.4 4.5 Q4.5 7.3 6.8 8.4 L8 7 L10.6 8 L10.6 10.2 Q9.8 11.6 8 11.4 Q1.4 10 0.4 2.6 Q0.6 0.8 2 0.5 Z" fill="var(--brand-green)"/></svg>
      <span>0491 638 205</span>
    </li>
    <li>
      <svg width="11" height="8" viewBox="0 0 11 8" aria-hidden="true"><rect width="11" height="8" fill="var(--brand-green)"/><path d="M0 0 L5.5 4.5 L11 0" stroke="#fff" stroke-width="1" fill="none"/></svg>
      <span>lionel@briskpropertydevelopments.com</span>
    </li>
    <li class="contact__address">Po Box 5347, Ferndale Central , Vic</li>
  </ul>
</section>

<section class="card card--back" aria-label="Business card back, white">
  <div class="wordmark">
    <span class="wordmark__square"></span>
    <span class="wordmark__name">Brisk Property<br>Developments</span>
  </div>
  <p class="website">www.<span class="website__accent">brisk</span>propertydevelopments.com</p>
</section>

<section class="card card--green" aria-label="Business card back, green">
  <div class="wordmark">
    <span class="wordmark__square"></span>
    <span class="wordmark__name">Brisk Property<br>Developments</span>
  </div>
  <p class="website">www.briskpropertydevelopments.com</p>
</section>

<section class="card card--red" aria-label="Business card back, red">
  <div class="wordmark">
    <span class="wordmark__square"></span>
    <span class="wordmark__name">Brisk Property<br>Developments</span>
  </div>
  <p class="website">www.briskpropertydevelopments.com</p>
</section>

</body>
</html>
```